Web Design for Independent Pet Supply shop.

Larch Critter Depot is a locally owned and operated premium natural pet food store and supply company with 2 thriving retail stores in Bend, Oregon, and a home delivery service. The pet food offered is the best on the market and may be described as “holistic”. Also on offer is a vast selection of toys, training tools, treats, and other supplies, as well as dog washing services that range from "do-it yourself" to "spa." Current site: LarchCritterDepot.com. They need a new, updated and responsive site.
Likes:
Tovanels.com: Natural colors, not loud, pages in motion, simple & clean but very informative.
Dorvikmerin.com: Everything in simple big colorful blocks. The specials run across the top and in motion. This site looks very professional but simple. The information is available several different places.
Plenharvest.com: Again big blocks through out. Very Fun and inviting. Tons of information with videos and recipes and testimonials. Pleasant feel and colors as well.
Dislikes:
Furlix.com: Looks cheap, hate the colors, very busy and over whelming. Hate the old style header bar going across with options. Too many printed words instead of fun images.
Colors should be "natural" tones, warm and soothing. Deep dark blue and greys with earthy wood color.
Do Not Use: Blue violet, violet, red violet

```html
<!DOCTYPE html>
<html lang="en">
<head>
<meta charset="utf-8">
<title>Larch Critter Depot</title>
<link href="https://fonts.googleapis.com/css2?family=Roboto:wght@300;400;500;700&family=Roboto+Condensed:wght@300;400;700&display=swap" rel="stylesheet">
<style>
:root{
  --brown:#c0843a;
  --brown-dark:#9c6a2c;
  --tan:#c7a86c;
  --tan-dark:#a98a52;
  --cream:#fdf1e3;
  --ink:#2b2b2b;
  --text:#6d6d6d;
  --charcoal:#262626;
  --charcoal-2:#1b1b1b;
  --orange:#e0982f;
  --white:#ffffff;
  --line:#e2e2e2;
}
*{box-sizing:border-box;margin:0;padding:0}
html,body{width:1200px;height:3462px;overflow:hidden}
body{font-family:"Roboto",Arial,sans-serif;color:var(--text);background:var(--white);position:relative}
section,header,footer,nav{position:absolute;left:0;width:1200px}

/* header */
.site-header{top:0;height:120px;background:var(--white)}
.brand{position:absolute;left:100px;top:42px;display:flex;align-items:center;gap:12px}
.brand-dot{width:30px;height:30px;border-radius:50%;background:var(--brown)}
.brand-name{font-weight:700;font-size:30px;color:var(--brown);letter-spacing:.5px}
.contact-bar{position:absolute;right:100px;top:38px;display:flex;align-items:center}
.phone-icon{width:44px;height:44px;border:2px solid #d8d8d8;border-radius:50%;display:flex;align-items:center;justify-content:center;margin-right:12px}
.phone-numbers{font-size:20px;color:var(--ink);margin-right:26px}
.social-box{width:30px;height:30px;border:1px solid #cfcfcf;margin-left:10px}

.main-nav{top:120px;height:69px;background:var(--tan);border-top:1px solid var(--tan-dark)}
.main-nav ul{list-style:none;display:flex;height:100%;padding-left:100px;padding-right:88px;justify-content:space-between}
.main-nav li{font-family:"Roboto Condensed",Arial,sans-serif;font-size:14px;color:var(--white);text-transform:uppercase;display:flex;align-items:center;padding:0 10px}
.main-nav li.active{background:var(--brown);padding:0 24px}

/* hero */
.hero{top:189px;height:556px}
.hero-photo{position:absolute;inset:0;background:linear-gradient(115deg,#4f6d28 0%,#8a9a3c 30%,#b27c42 48%,#6f8a34 70%,#39531e 100%)}
.hero-copy{position:absolute;left:100px;top:288px;color:var(--white);font-family:"Roboto Condensed",Arial,sans-serif;line-height:1.2}
.hero-copy .line-light{font-weight:300;font-size:40px;display:block}
.hero-copy .line-bold{font-weight:400;font-size:40px;display:block}
.slider-dots{position:absolute;top:506px;left:0;width:100%;display:flex;justify-content:center;gap:18px}
.slider-dots span{width:14px;height:14px;border-radius:50%;background:var(--white)}
.slider-dots span.on{background:var(--ink)}

/* generic blocks */
.section-title{font-size:36px;font-weight:700;color:var(--brown);line-height:1.2;margin-bottom:26px}
.body-text{font-size:13px;line-height:1.75;color:var(--text);margin-bottom:18px}
.btn-dark{display:inline-block;background:var(--ink);color:var(--white);font-size:12px;font-weight:500;text-transform:uppercase;padding:16px 24px;border-radius:4px;margin-top:12px}

.dogwash{top:745px;height:478px;background:var(--cream)}
.dogwash-main{position:absolute;left:100px;top:30px;width:590px}
.dogwash-main .section-title{margin-bottom:18px}
.dogwash-main .body-text{font-size:11.5px;line-height:1.6;margin-bottom:12px}
.dogwash-main .btn-dark{margin-top:4px}
.welcome-card{position:absolute;left:718px;top:48px;width:382px}
.welcome-photo{height:228px;border:4px solid var(--white);background:linear-gradient(180deg,#6d7f92 0%,#a58e63 55%,#7a6a50 100%)}
.welcome-card h3{font-size:21px;font-weight:500;color:var(--brown);margin:14px 0 8px}
.welcome-card p{font-size:12px;line-height:1.6}
.link-more{display:block;font-size:11px;color:var(--brown);margin-top:10px;text-transform:uppercase}

.grog{top:1223px;height:577px;background:var(--white)}
.grog-copy{position:absolute;left:100px;top:102px;width:545px}
.grog-photo{position:absolute;left:640px;top:0;width:560px;height:577px;background:radial-gradient(ellipse at 55% 50%,#d9a35c 0%,#e9c594 38%,#ffffff 72%)}

.lawsuit{top:1800px;height:577px;background:var(--cream)}
.lawsuit-photo{position:absolute;left:0;top:0;width:580px;height:577px;background:radial-gradient(ellipse at 45% 50%,#c9a884 0%,#ead3b6 40%,#fdf1e3 74%)}
.lawsuit-copy{position:absolute;left:633px;top:104px;width:470px}

.leads{top:2377px;height:381px;background:linear-gradient(180deg,#4a4a4a,#3a3a3a)}
.leads-photo{position:absolute;left:600px;top:0;width:600px;height:381px;background:linear-gradient(180deg,#7f8b94 0%,#a0a6a8 50%,#5a5a56 100%);clip-path:polygon(14% 0,100% 0,100% 100%,0 100%)}
.leads-copy{position:absolute;left:100px;top:34px;width:560px;color:#e5e5e5}
.leads-copy .section-title{margin-bottom:10px}
.leads-sub{font-size:17px;font-weight:700;color:var(--white);line-height:1.5;margin-bottom:12px}
.leads-copy .body-text{color:#d0d0d0;font-size:12px;line-height:1.65;margin-bottom:12px}

.signup{top:2758px;height:238px;background:linear-gradient(180deg,#1d2633 0%,#2b3444 60%,#1a1f28 100%)}
.signup h2{position:absolute;left:100px;top:20px;font-size:34px;font-weight:500;color:var(--white)}
.signup p{position:absolute;left:100px;top:74px;width:560px;font-size:12.5px;line-height:1.6;color:#d4d4d4}
.delivery-box{position:absolute;left:740px;top:32px;width:360px;height:54px;border:1px solid #8a8f98;border-radius:6px;display:flex;align-items:center;justify-content:center;gap:12px;color:var(--white);font-size:16px;font-weight:500}
.delivery-box b{color:var(--orange);font-size:24px;font-weight:500}
.field{position:absolute;top:136px;height:62px;border:1px solid #8a8f98;border-radius:4px;padding:0 20px;display:flex;align-items:center;font-size:13px;color:#a4a8ae}
.field.name{left:100px;width:380px}
.field.email{left:512px;width:372px}
.btn-cta{position:absolute;left:916px;top:136px;width:184px;height:62px;background:var(--orange);color:var(--white);font-size:19px;font-weight:500;display:flex;align-items:center;justify-content:center;border-radius:3px}

.partners{top:2996px;height:184px;background:var(--white)}
.partner-row{position:absolute;left:96px;top:46px;display:flex;gap:24px}
.partner-badge{width:190px;height:94px;border:1px solid var(--line);display:flex;align-items:center;justify-content:center}
.partner-badge span{width:130px;height:26px;background:#d9dde3;border-radius:3px}

.site-footer{top:3180px;height:236px;background:var(--charcoal)}
.footer-col{position:absolute;top:36px;color:#cfcfcf}
.footer-col h4{font-size:16px;font-weight:500;color:var(--white);text-transform:uppercase;margin-bottom:18px}
.footer-col ul{list-style:none}
.footer-col li{font-size:12px;line-height:1.85;color:#e0e0e0}
.footer-col p{font-size:11px;line-height:1.55;color:#bdbdbd;margin-bottom:8px;width:240px}
.icon-row{display:flex;align-items:center;gap:10px}
.icon-sq{width:10px;height:10px;background:var(--orange);display:inline-block}
.copyright{position:absolute;left:0;width:1200px;top:3416px;height:46px;background:var(--charcoal-2);display:flex;align-items:center;justify-content:center;font-size:12px;color:#a6a6a6}
</style>
</head>
<body>

<header class="site-header">
  <div class="brand"><span class="brand-dot"></span><span class="brand-name">Larch Critter Depot</span></div>
  <div class="contact-bar">
    <span class="phone-icon">
      <svg width="20" height="20" viewBox="0 0 24 24"><path d="M6.6 10.8a15 15 0 0 0 6.6 6.6l2.2-2.2a1 1 0 0 1 1-.25 11 11 0 0 0 3.6.6 1 1 0 0 1 1 1V20a1 1 0 0 1-1 1A17 17 0 0 1 3 4a1 1 0 0 1 1-1h3.5a1 1 0 0 1 1 1 11 11 0 0 0 .6 3.6 1 1 0 0 1-.25 1z" fill="#3a3a3a"/></svg>
    </span>
    <span class="phone-numbers">541-555-0182, 541-555-0147</span>
    <span class="social-box"></span><span class="social-box"></span><span class="social-box"></span><span class="social-box"></span>
  </div>
</header>

<nav class="main-nav">
  <ul>
    <li class="active">Home</li><li>Events</li><li>Blog</li><li>About</li><li>Dog Wash</li><li>Products</li><li>Resources</li><li>Links</li><li>Contact</li>
  </ul>
</nav>

<section class="hero">
  <div class="hero-photo" role="img" aria-label="Puppy eating from a blue bowl on green grass"></div>
  <div class="hero-copy">
    <span class="line-light">DEDICATED TO A BETTER</span>
    <span class="line-bold">DIET FOR A HEALTHIER PET</span>
  </div>
  <div class="slider-dots"><span></span><span class="on"></span><span></span></div>
</section>

<section class="dogwash">
  <div class="dogwash-main">
    <h2 class="section-title">The Larch Critter Depot Dog Wash<br>News and Updates</h2>
    <p class="body-text">The Larch Critter Depot Dog Wash attendants are always here to help wash your four-legged friends, and trim their nails...but they are also here to help educate all of us! Nail trims are such an essential routine for our pups, especially if they don't run and walk as much as they would in the wild.</p>
    <p class="body-text">Below are two photos that demonstrate how important nail trims are. The 'Before' shot shows the dog's two front feet. Looking at the photo the left foot ( Dog's right foot) has not been trimmed yet. Notice the two outside toes twisting out and away from the foot. The right foot ( Dog's left foot ) has already been trimmed. Notice how "cat like" the toes are, tight and together allowing the pads full access to the ground in a healthy way. Dog toe/foot pads relay information to the dog like where the ground is, what angle the slope/stairs are, etc. When toes get twisted due to long nails, signals get mixed and dogs start trying to compensate by standing differently resulting in more strain in their skeletal structure.</p>
    <span class="btn-dark">Read More</span>
  </div>
  <div class="welcome-card">
    <div class="welcome-photo" role="img" aria-label="Store interior with stocked pet food shelves"></div>
    <h3>Welcome to Larch Critter Depot!</h3>
    <p>We are a locally owned and operated premium natural pet food store and supply company. The whole idea for Larch Critter Depot started back in 1993 when Mara Ellwood's (owner) dog became sick due to a food allergy. Upon discovering very few options for purchasing premium.</p>
    <span class="link-more">Read More</span>
  </div>
</section>

<section class="grog">
  <div class="grog-copy">
    <h2 class="section-title">Pup Pour</h2>
    <p class="body-text">Now you can pour some cold brew for your pup in a fun and easy way that has a delicious flavor and packed full of vegetarian K9 specific glucosamine with essential vitamins and minerals for your dogs health and well being.</p>
    <p class="body-text">Have you ever wanted to share a cold one with your best friend? Now you can pour some cold brew in a fun and easy way that has a delicious flavor and packed full of vegetarian K9 specific glucosamine with essential vitamins and minerals for your dogs health and well being.</p>
    <span class="btn-dark">Read More</span>
  </div>
  <div class="grog-photo" role="img" aria-label="Golden retriever puppy sitting on a white backdrop"></div>
</section>

<section class="lawsuit">
  <div class="lawsuit-photo" role="img" aria-label="Pug sitting beside a patterned bowl of kibble"></div>
  <div class="lawsuit-copy">
    <h2 class="section-title">Granvel Lawsuit</h2>
    <p class="body-text">IN NEWS: Granvel is being sued by , Owen Castel of Harbor Point, California. He he first purchased Brightbowl food in December or January. Since, he has witnessed one of his dogs pass away and 2 of his dogs get sick. PLEASE read and watch this link for more information!</p>
    <p class="body-text">The named plaintiff in the suit describes how one of his dogs died after eating Brightbowl and two of his dogs got sick. In the past four years, consumers have made more than 3,000 online complaints about dogs becoming ill or dying after eating Brightbowl, the lawsuit says.</p>
    <span class="btn-dark">Read More</span>
  </div>
</section>

<section class="leads">
  <div class="leads-photo" role="img" aria-label="Woman and black dog sitting side by side on a rocky shore"></div>
  <div class="leads-copy">
    <h2 class="section-title">Driftline 5/8" Leads On Sale</h2>
    <p class="leads-sub">Your local Driftline has ALL of their 5/8"<br>Leads ON SALE for just $10</p>
    <p class="body-text">There are many variations of passages of Lorem Ipsum available, but the majority have suffered alteration in some form, by injected humour, or randomised words which don't look even slightly believable. If you are going to use a passage of Lorem Ipsum, you need to be sure there isn't anything embarrassing hidden in the middle of text. All the Lorem Ipsum generators on the Internet tend to repeat predefined chunks as necessary, making this the first true generator on the Internet.</p>
    <span class="btn-dark">Read More</span>
  </div>
</section>

<section class="signup">
  <h2>SIGN UP</h2>
  <p>Denouncing pleasure and praising pain was born and I will give you a complete account of the system, actual teachings of the great explorer of the truth, the master-builder of human happiness.</p>
  <div class="delivery-box">Free Home delivery : <b>541-555-0182</b></div>
  <div class="field name">Your Name *</div>
  <div class="field email">E-mail ID *</div>
  <div class="btn-cta">CLICK HERE</div>
</section>

<section class="partners">
  <div class="partner-row">
    <div class="partner-badge"><span></span></div>
    <div class="partner-badge"><span></span></div>
    <div class="partner-badge"><span></span></div>
    <div class="partner-badge"><span></span></div>
    <div class="partner-badge"><span></span></div>
  </div>
</section>

<footer class="site-footer">
  <div class="footer-col" style="left:98px">
    <h4>Home</h4>
    <ul><li>Events</li><li>Blog</li><li>About</li><li>Dog Wash</li><li>Products</li><li>Resources...</li></ul>
  </div>
  <div class="footer-col" style="left:255px">
    <h4>Blog</h4>
    <p>Fresh notes on natural diets, grooming tips and store news from our team.</p>
    <p>Seasonal care ideas, new arrivals and simple training advice for your pets.</p>
    <p>Stories from our dog wash and tips for happy, healthy companions.</p>
  </div>
  <div class="footer-col" style="left:548px">
    <h4>Policies</h4>
    <ul><li>Contact</li><li>Return Policy</li><li>Privacy Policy</li><li>Employment</li><li>Staff Login</li></ul>
  </div>
  <div class="footer-col" style="left:706px">
    <h4>Contact Us</h4>
    <ul>
      <li class="icon-row"><span class="icon-sq"></span>eastside@larchcritterdepot.com</li>
      <li class="icon-row"><span class="icon-sq"></span>+ 541-555-0182</li>
      <li class="icon-row"><span class="icon-sq"></span>+ 541-555-0147</li>
    </ul>
  </div>
  <div class="footer-col" style="left:1002px">
    <h4>Follow Us</h4>
    <ul>
      <li class="icon-row"><span class="icon-sq"></span>PAWBOOK</li>
      <li class="icon-row"><span class="icon-sq"></span>CHIRPER</li>
      <li class="icon-row"><span class="icon-sq"></span>VIEWTUBE</li>
      <li class="icon-row"><span class="icon-sq"></span>SNAPGRAM</li>
    </ul>
  </div>
</footer>
<div class="copyright">© Copyright 2015-2016. LarchCritterDepot.com - All rights reserved.</div>

</body>
</html>
```